Web Design for an Innovative Life Science Marketplace

IMPORTANT:
The software is called CS-Cart. It has capabilities and limitations with design features in the software. There is a certain framework that needs to be followed. It is PHP and Linux. It may require add-ons for your design, so please be specific with what is required. It’s preferred the designer has CS-Cart knowledge/experience.

Key Requirements
1. I’d like the design to include an implemented/recommended CS-Cart theme that is consistent with our branding (see the marketing collateral and logo).
2. I then need the additional design changes to that theme to create the below web pages.
3. All designs should be consistent with our branding. All pictures should either be computer generated (clip art-like) or pictures of happy patients. What is a happy patient? Close up photo of someone healthy, happy, and experiencing/enjoying life. Not someone in a hospital or getting care. Please see examples already on the site.

Please see the attached Web Design details in the word document. That document is important to complete the design.

```html
<!DOCTYPE html>
<html lang="en">
<head>
<meta charset="utf-8">
<title>Our Platform – Vialink</title>
<link href="https://fonts.googleapis.com/css2?family=Roboto:wght@400;500;700&family=Roboto+Condensed:wght@400;700&display=swap" rel="stylesheet">
<style>
:root{
  --teal:#1c9a89;
  --teal-dark:#15877a;
  --green:#8dc63f;
  --ink:#333;
  --muted:#6b6b6b;
  --line:#dcdcdc;
  --footer:#2a2a2a;
  --white:#fff;
}
*{box-sizing:border-box;margin:0;padding:0}
html,body{width:727px;height:1200px;overflow:hidden;background:var(--white);font-family:Roboto,Arial,sans-serif;color:var(--ink)}
.page{position:relative;width:727px;height:1200px}
.abs{position:absolute}

.topbar{top:0;left:0;width:727px;height:16px;font-size:6px;color:#555;text-transform:uppercase}
.topbar .item{position:absolute;top:4px;display:flex;align-items:center;gap:4px}
.topbar .dot{width:6px;height:6px;background:var(--teal);border-radius:1px}
.pill{position:absolute;top:2px;height:13px;border-radius:7px;color:#fff;font-size:6px;font-weight:700;display:flex;align-items:center;justify-content:center}
.pill.login{left:539px;width:38px;background:var(--teal)}
.pill.register{left:580px;width:49px;background:var(--green)}

.header{top:16px;left:0;width:727px;height:48px;border-top:1px solid #eee}
.brand{position:absolute;left:98px;top:14px;display:flex;align-items:center;gap:5px}
.brand .mark{width:16px;height:16px;border-radius:50%;background:var(--teal)}
.brand .name{font-family:"Roboto Condensed",sans-serif;font-weight:700;font-size:17px;color:var(--teal);letter-spacing:.5px}
.cart{position:absolute;left:384px;top:12px;display:flex;gap:6px;align-items:center}
.cart .icon{width:31px;height:26px;background:var(--green);display:flex;align-items:center;justify-content:center}
.cart .label{font-family:"Roboto Condensed",sans-serif;font-size:10px;color:#555;line-height:1}
.cart .label b{font-size:14px;color:var(--green)}
.cart .label small{font-size:6px}
.search{position:absolute;left:510px;top:14px;width:119px;height:20px;border-radius:10px;background:#f3f3f3;font-size:6px;color:#aaa;padding:7px 0 0 10px}
.search .go{position:absolute;right:4px;top:3px;width:14px;height:14px;border-radius:50%;background:var(--green)}

.nav{top:64px;left:0;width:727px;height:24px;background:var(--teal);display:flex;padding-left:84px}
.nav a{font-family:"Roboto Condensed",sans-serif;font-size:7px;font-weight:700;color:#fff;text-decoration:none;padding:0 14px;line-height:24px;border-right:1px solid rgba(255,255,255,.15)}
.nav a.active{color:var(--green)}

.hero{top:88px;left:0;width:727px;height:142px;background:linear-gradient(180deg,#c9c2b4 0%,#b08f72 55%,#6f5237 100%)}
.hero-title{top:128px;left:98px;display:flex;align-items:baseline;color:#fff;font-family:"Roboto Condensed",sans-serif;font-weight:700}
.hero-title .rule{width:18px;height:2px;background:#fff;margin-right:3px;align-self:center}
.hero-title .cap{font-size:56px;line-height:48px}
.hero-title .rest{font-size:21px}
.hero-title .rule2{width:46px;height:2px;background:#fff;margin-left:5px;align-self:center}

.intro{top:264px;left:98px;width:532px;font-size:7px;line-height:11px;color:var(--muted)}
.intro p+p{margin-top:11px}

.acc{left:98px;width:532px;height:32px;border:1px solid var(--line);font-size:7.5px;color:#444;display:flex;align-items:center;padding-left:11px}
.acc::before{content:"";border-left:3px solid #444;border-top:2.5px solid transparent;border-bottom:2.5px solid transparent;margin-right:5px}

.feature{width:258px;height:58px}
.feature svg.frame{position:absolute;left:0;top:0}
.feature .txt{position:absolute;font-family:"Roboto Condensed",sans-serif;font-size:12px;line-height:12px;font-weight:500}
.feature .txt b{font-family:Roboto,sans-serif;font-size:34px;font-weight:700;line-height:28px;vertical-align:-2px}
.tick{position:absolute;width:18px;height:18px;border-radius:50%;display:flex;align-items:center;justify-content:center}

.band{top:786px;left:0;width:727px;height:89px;background:linear-gradient(90deg,#86c23a,#9acd4a,#86c23a)}
.contact{position:absolute;top:20px;display:flex;align-items:center;gap:8px;color:#fff}
.contact .ring{width:42px;height:42px;border:2px solid #fff;border-radius:50%;display:flex;align-items:center;justify-content:center}
.contact b{font-size:10px;display:block}
.contact small{font-size:6px;font-weight:700;text-transform:uppercase}

.footer{top:875px;left:0;width:727px;height:293px;background:var(--footer);color:#fff}
.heading{position:absolute;font-family:"Roboto Condensed",sans-serif;font-weight:700;font-size:14px;display:flex;align-items:flex-end}
.heading b{font-size:34px;line-height:28px;color:var(--teal)}
.social{position:absolute;top:63px;left:327px;display:flex;gap:4px}
.social span{width:22px;height:22px;border:1px solid #ddd;border-radius:2px}
.underline{position:absolute;width:14px;height:2px;background:#fff}
.email{position:absolute;left:97px;top:164px;width:148px;height:26px;border-radius:13px;background:#ddd;font-size:6px;color:#666;padding:10px 0 0 14px}
.subscribe{position:absolute;left:101px;top:193px;width:78px;height:19px;border-radius:10px;background:var(--teal);font-size:7.5px;font-weight:700;text-align:center;line-height:19px}
.post{position:absolute;left:281px;width:152px;font-size:7.5px;line-height:10px;color:#aaa;padding-bottom:7px;border-bottom:1px solid #3c3c3c}
.post a{color:var(--teal)}
.map{position:absolute;left:459px;top:164px;width:164px;height:90px;background:linear-gradient(135deg,#e9e6dc 0%,#d9dccd 55%,#a9c4e0 75%,#9dbddc 100%)}

.bottombar{top:1168px;left:0;width:727px;height:32px;background:var(--teal);color:#fff;font-size:6px}
.bottombar nav{position:absolute;left:104px;top:13px;display:flex;gap:20px}
.bottombar .copy{position:absolute;right:98px;top:13px;text-transform:uppercase}
</style>
</head>
<body>
<div class="page">

  <div class="abs topbar">
    <div class="item" style="left:98px"><span class="dot"></span>Adress : 48 Sample Avenue, NY</div>
    <div class="item" style="left:242px"><span class="dot"></span>Email : hello@vialinkqc.com</div>
    <div class="item" style="left:373px"><span class="dot"></span>Call us : <span style="font-size:7px">555-014-2290</span></div>
    <div class="item" style="left:479px"><span class="dot" style="border-radius:50%"></span>My account</div>
    <div class="pill login">LOGIN</div>
    <div class="pill register">REGISTER</div>
  </div>

  <header class="abs header">
    <div class="brand"><span class="mark"></span><span class="name">VIALINK</span></div>
    <div class="cart">
      <div class="icon">
        <svg width="20" height="16" viewBox="0 0 20 16" fill="none" stroke="#fff" stroke-width="1.5"><path d="M1 2h3l2 8h10l2-6H5"/><circle cx="8" cy="13.5" r="1.3"/><circle cx="15" cy="13.5" r="1.3"/></svg>
      </div>
      <div class="label">SHOPPING CART<br><b>(0)</b> <small>ITEM SELECTED</small></div>
    </div>
    <div class="search">Search Product...<span class="go"></span></div>
  </header>

  <nav class="abs nav">
    <a>HOME</a><a>ABOUT US</a><a>HOW IT WORKS</a><a class="active">OUR PLATFORM</a><a>BENEFITS</a><a>CONTACT US</a>
  </nav>

  <div class="abs hero" role="img" aria-label="Photo of a happy person raising arms at sunset over the hills"></div>
  <h1 class="abs hero-title"><span class="rule"></span><span class="cap">O</span><span class="rest">UR PLATFORM</span><span class="rule2"></span></h1>

  <div class="abs intro">
    <p>Proin pharetra sollicitudin malesuada. Aenean tristique, sem a pellentesque iaculis, quam risus egestas lorem, ac dapibus turpis orci eget lectus. Vivamus nec odio suscipit, fermentum leo vel, mattis massa. Orci varius natoque penatibus et magnis dis parturient montes, nascetur ridiculus mus.</p>
    <p>Proin pharetra sollicitudin malesuada. Aenean tristique, sem a pellentesque iaculis, quam risus egestas lorem, ac dapibus turpis orci eget lectus. Vivamus nec odio suscipit, fermentum leo vel, mattis massa. Orci varius natoque penatibus et magnis dis parturient montes, nascetur ridiculus mus. Interdum et malesuada fames ac ante ipsum primis in faucibus. Maecenas at diam quis turpis consequat vulputate non ac elit Proin convallis mattis nunc Interdum et malesuada fames.....</p>
  </div>

  <div class="abs acc" style="top:365px">A virtual multi-vendor marketplace for the life science community to conncet and transact pre-market and after-market materials and equipment</div>
  <div class="abs acc" style="top:401px"><b>Researchers,manufacturers,</b>and original suppliers can create an account to buy,sell, or danate materials</div>

  <div class="abs feature" style="left:98px;top:454px">
    <svg class="frame" width="258" height="58"><polyline points="28,0.5 257.5,0.5 257.5,57.5 28,57.5" fill="none" stroke="var(--teal)"/><polyline points="28,0.5 8,24" fill="none" stroke="var(--teal)"/><polyline points="8,34 28,57.5" fill="none" stroke="var(--teal)"/></svg>
    <div class="tick" style="left:-7px;top:20px;background:var(--teal)"><svg width="9" height="7"><path d="M1 3.5l2.5 2.5L8 1" stroke="#fff" stroke-width="1.6" fill="none"/></svg></div>
    <div class="txt" style="left:35px;top:10px;color:var(--teal)"><b>A</b>uthentication and terms of quality</div>
  </div>
  <div class="abs feature" style="left:372px;top:454px">
    <svg class="frame" width="258" height="58"><polyline points="230,0.5 0.5,0.5 0.5,57.5 230,57.5" fill="none" stroke="var(--green)"/><polyline points="230,0.5 250,24" fill="none" stroke="var(--green)"/><polyline points="250,34 230,57.5" fill="none" stroke="var(--green)"/></svg>
    <div class="tick" style="left:243px;top:20px;background:var(--green)"><svg width="9" height="7"><path d="M1 3.5l2.5 2.5L8 1" stroke="#fff" stroke-width="1.6" fill="none"/></svg></div>
    <div class="txt" style="left:12px;top:10px;color:var(--green)"><b>S</b>etup store</div>
  </div>
  <div class="abs feature" style="left:98px;top:524px">
    <svg class="frame" width="258" height="58"><polyline points="28,0.5 257.5,0.5 257.5,57.5 28,57.5" fill="none" stroke="var(--teal)"/><polyline points="28,0.5 8,24" fill="none" stroke="var(--teal)"/><polyline points="8,34 28,57.5" fill="none" stroke="var(--teal)"/></svg>
    <div class="tick" style="left:-7px;top:20px;background:var(--teal)"><svg width="9" height="7"><path d="M1 3.5l2.5 2.5L8 1" stroke="#fff" stroke-width="1.6" fill="none"/></svg></div>
    <div class="txt" style="left:35px;top:6px;color:var(--teal)"><b>S</b>eamlessly transact and request<br><span style="padding-left:23px">for information</span></div>
  </div>
  <div class="abs feature" style="left:372px;top:524px">
    <svg class="frame" width="258" height="58"><polyline points="230,0.5 0.5,0.5 0.5,57.5 230,57.5" fill="none" stroke="var(--green)"/><polyline points="230,0.5 250,24" fill="none" stroke="var(--green)"/><polyline points="250,34 230,57.5" fill="none" stroke="var(--green)"/></svg>
    <div class="tick" style="left:243px;top:20px;background:var(--green)"><svg width="9" height="7"><path d="M1 3.5l2.5 2.5L8 1" stroke="#fff" stroke-width="1.6" fill="none"/></svg></div>
    <div class="txt" style="left:12px;top:10px;color:var(--green)"><b>C</b>heckout and sign</div>
  </div>

  <div class="abs acc" style="top:599px">cGMP quality focused platform</div>
  <div class="abs acc" style="top:635px">Part 11 compliant signature and account authentication</div>
  <div class="abs acc" style="top:670px">Leverages industry auditing skills to facilitate compiant and transparent transactions</div>
  <div class="abs acc" style="top:706px">Some of the best and industry vendors and software used</div>

  <section class="abs band" role="img" aria-label="Green tinted photo of smiling people behind contact details">
    <div class="contact" style="left:104px">
      <div class="ring"><svg width="18" height="18" viewBox="0 0 24 24" fill="#fff"><path d="M6.6 10.8a15.2 15.2 0 006.6 6.6l2.2-2.2a1 1 0 011-.25 11.4 11.4 0 003.6.57 1 1 0 011 1V20a1 1 0 01-1 1A17 17 0 013 4a1 1 0 011-1h3.5a1 1 0 011 1c0 1.25.2 2.45.57 3.57a1 1 0 01-.25 1z"/></svg></div>
      <div><b>555-014-2290</b><small>Call us for enquiry</small></div>
    </div>
    <div class="contact" style="left:283px">
      <div class="ring"><svg width="18" height="14" viewBox="0 0 18 14" fill="none" stroke="#fff" stroke-width="1.3"><rect x="1" y="1" width="16" height="12"/><path d="M1 1l8 7 8-7M1 13l6-6M17 13l-6-6"/></svg></div>
      <div><b>hello@vialinkqc.com</b><small>Drop us a line anytime!</small></div>
    </div>
    <div class="contact" style="left:481px">
      <div class="ring"><svg width="14" height="18" viewBox="0 0 14 18" fill="#fff"><path d="M7 0a7 7 0 00-7 7c0 5 7 11 7 11s7-6 7-11a7 7 0 00-7-7zm0 9.5A2.5 2.5 0 117 4.5a2.5 2.5 0 010 5z"/></svg></div>
      <div><b>48 Sample Avenue, NY</b><small>Company address</small></div>
    </div>
  </section>

  <footer class="abs footer">
    <div class="heading" style="left:292px;top:25px"><b>C</b>ONNECT WITH US</div>
    <div class="social" aria-label="Social links"><span></span><span></span><span></span></div>

    <div class="heading" style="left:96px;top:115px"><b>N</b>EWSLETTER</div>
    <div class="underline" style="left:98px;top:146px"></div>
    <div class="email">ENTER YOUR EMAIL ID</div>
    <div class="subscribe">SUBSCRIBE</div>

    <div class="heading" style="left:282px;top:115px"><b>T</b>IMELINE</div>
    <div class="underline" style="left:284px;top:146px"></div>
    <p class="post" style="top:162px"><a>@vialink_qc:</a> Phasellus dapibus tellus at nibh lobortis, vitae placerat sapien tempor.</p>
    <p class="post" style="top:196px"><a>@vialink_qc:</a> Phasellus dapibus tellus at nibh lobortis, vitae placerat sapien tempor.</p>
    <p class="post" style="top:230px;border-bottom:none"><a>@vialink_qc:</a> Phasellus dapibus tellus at nibh lobortis, vitae placerat sapien tempor.</p>

    <div class="heading" style="left:457px;top:115px"><b>L</b>OCATION</div>
    <div class="underline" style="left:459px;top:146px"></div>
    <div class="map" role="img" aria-label="Street map of the company location"></div>
  </footer>

  <div class="abs bottombar">
    <nav><span>HOME</span><span>ABOUT US</span><span>HOW IT WORKS</span><span>OUR PLATFORM</span><span>BENEFITS</span><span>CONTACT US</span></nav>
    <div class="copy">© 2018 Vialink . All rights reserved</div>
  </div>

</div>
</body>
</html>
```